BRIARWELL TAVERN FRIDAY MAY 3

Flyer design for bar/nightclub event. Trying to keep a general theme with their flyers (see below) but would like to add some neon or some pop to it.

TEXT:

Briarwell Bar & Tavern Presents

LANTERNTIDE NIGHTS
GRAND OPENING EVENT

PURE HOUSE MUSIC W/

MORVEX
TOMAS HALVERO
BENNAR & ACE DRIFTWAY

21+
9PM-130AM
518 M AVENUE DAVIS CA

Target Market(s)

House/dance music crowd.

Industry/Entity Type

Night Club

Font styles to use
Sans Serif

Colors
9bcb3c
fbee3d
ffffff

Requirements
Must have
• Large DJ names
Nice to have
• General theme of the attached flyers. Neon colors that stick with the theme. Anything else that looks cool will be considered

```html
<!DOCTYPE html>
<html lang="en">
<head>
<meta charset="utf-8">
<title>Lanterntide Nights — Grand Opening</title>
<link rel="stylesheet" href="https://fonts.googleapis.com/css2?family=Montserrat:wght@700;800&family=Questrial&display=swap">
<style>
  :root {
    --bark: #3b2e25;
    --neon-yellow: #fbee3d;
    --lime: #9bcb3c;
    --leaf: #b5dc45;
    --moss: #7e8a3c;
    --white: #ffffff;
    --glow-yellow: rgba(251, 238, 61, 0.85);
    --glow-lime: rgba(155, 203, 60, 0.9);
  }
  html, body { margin: 0; padding: 0; overflow: hidden; background: var(--bark); }
  .flyer {
    position: relative;
    width: 849px;
    height: 1200px;
    overflow: hidden;
    background: var(--bark);
    font-family: "Questrial", "Century Gothic", sans-serif;
    color: var(--bark);
  }
  .canopy {
    position: absolute; left: 0; top: 0; width: 849px; height: 180px;
    background: linear-gradient(180deg, #d4ea55 0%, var(--leaf) 100%);
  }
  .canopy-tree {
    position: absolute; top: 0; width: 285px; height: 190px;
    background: radial-gradient(ellipse at 50% 45%, rgba(110,140,40,0.55) 0%, rgba(110,140,40,0) 70%);
  }
  .canopy-tree.left { left: 0; }
  .canopy-tree.right { right: 0; }
  .venue-mark {
    position: absolute; left: 174px; top: 52px; width: 500px;
    display: flex; align-items: center; justify-content: center; gap: 12px;
    white-space: nowrap;
    font-family: "Montserrat", sans-serif; font-weight: 800;
    font-size: 25px; letter-spacing: 1px; color: var(--bark);
  }
  .venue-mark .mark-square { width: 18px; height: 18px; background: var(--bark); flex: none; }
  .presents {
    position: absolute; left: 0; top: 100px; width: 849px; margin: 0;
    text-align: center; font-size: 24px; letter-spacing: 8px; color: var(--bark);
  }
  .series-title {
    position: absolute; left: 40px; top: 196px; margin: 0;
    font-weight: 400; font-size: 54px; line-height: 60px;
    color: var(--neon-yellow); letter-spacing: 1px;
    text-shadow: 0 0 6px var(--glow-yellow), 0 0 18px var(--glow-yellow), 0 0 34px rgba(251,238,61,0.5);
  }
  .bar {
    position: absolute; left: 14px; width: 824px;
    background: linear-gradient(90deg, var(--neon-yellow) 0%, var(--lime) 100%);
    display: flex; align-items: center;
    box-shadow: 0 0 10px var(--glow-yellow), 0 0 22px rgba(155,203,60,0.55);
  }
  .event-bar { top: 266px; height: 64px; padding-left: 26px; box-sizing: border-box; font-size: 52px; white-space: nowrap; }
  .event-bar strong { font-family: "Montserrat", sans-serif; font-weight: 700; font-size: 50px; margin-right: 14px; }
  .music-block {
    position: absolute; left: 14px; top: 353px; width: 824px; height: 120px;
    background: linear-gradient(90deg, var(--leaf) 0%, var(--lime) 100%);
    box-shadow: 0 0 14px var(--glow-lime);
  }
  .music-block p { margin: 0; position: absolute; left: 26px; top: 14px; font-size: 50px; white-space: nowrap; }
  .headliner {
    position: absolute; left: 0; width: 849px; top: 484px; margin: 0; text-align: center;
    font-family: "Montserrat", sans-serif; font-weight: 800; font-size: 64px;
    color: var(--neon-yellow); letter-spacing: 4px;
    text-shadow: 0 0 8px var(--glow-yellow), 0 0 22px var(--glow-yellow), 0 0 42px rgba(251,238,61,0.55);
  }
  .dj-bar {
    justify-content: center; height: 57px; white-space: nowrap;
    font-family: "Montserrat", sans-serif; font-weight: 800; font-size: 50px; letter-spacing: 2px;
  }
  .dj-1 { top: 566px; }
  .dj-2 { top: 638px; }
  .dj-3 { top: 715px; }
  .forest-floor {
    position: absolute; left: 0; top: 800px; width: 849px; height: 400px;
    background: linear-gradient(180deg, var(--lime) 0%, #8fae3a 60%, var(--moss) 100%);
  }
  .treeline {
    position: absolute; right: 0; top: 885px; width: 210px; height: 315px;
    background: linear-gradient(180deg, rgba(110,130,50,0) 0%, rgba(110,130,50,0.7) 45%, rgba(110,120,55,0.9) 100%);
  }
  .details {
    position: absolute; left: 11px; top: 840px; width: 644px; height: 254px;
    background: var(--bark);
    box-shadow: 0 0 0 3px var(--neon-yellow), 0 0 20px var(--glow-yellow);
  }
  .details .bar {
    left: 3px; width: 627px; padding-left: 32px; box-sizing: border-box;
    font-size: 44px; white-space: nowrap; box-shadow: none;
  }
  .d-age { top: 22px; height: 46px; }
  .d-date { top: 76px; height: 49px; }
  .d-time { top: 129px; height: 52px; }
  .d-place { top: 188px; height: 55px; }
</style>
</head>
<body>
<main class="flyer">
  <header class="canopy">
    <div class="canopy-tree left" role="img" aria-label="Leafy tree branches in the upper left corner"></div>
    <div class="canopy-tree right" role="img" aria-label="Leafy tree branches in the upper right corner"></div>
    <div class="venue-mark"><span class="mark-square"></span><span>BRIARWELL BAR &amp; TAVERN</span></div>
    <p class="presents">PRESENTS</p>
  </header>

  <h1 class="series-title">LANTERNTIDE NIGHTS</h1>
  <div class="bar event-bar"><strong>GRAND OPENING</strong>EVENT</div>
  <div class="music-block"><p>PURE HOUSE MUSIC W/</p></div>

  <h2 class="headliner">MORVEX</h2>
  <div class="bar dj-bar dj-1">TOMAS HALVERO</div>
  <div class="bar dj-bar dj-2">BENNAR</div>
  <div class="bar dj-bar dj-3">&amp; ACE DRIFTWAY</div>

  <div class="forest-floor"></div>
  <div class="treeline" role="img" aria-label="Silhouette of pine trees along the lower right edge"></div>

  <section class="details">
    <div class="bar d-age">21+</div>
    <div class="bar d-date">FRIDAY MAY 3 2019</div>
    <div class="bar d-time">9PM-130AM</div>
    <div class="bar d-place">518 M AVENUE DAVIS CA</div>
  </section>
</main>
</body>
</html>
```